Pelican HVAC WordPress website design

Design a new modern, clean, website for HVAC mechanical business that uses company logo/colors for branding and recognition. Files attached are just for band and color information. Here is a website design that appeals to me https://www.corvellsupply.example/

A clear description of who we are and what we do

An easily-navigated site map

An easily-navigated site map for mobile devices

Easy-to-find contact information

Obvious call to action for service, installs or to schedule estimates

about us page

Provide a way for potential customers to contact us via text or email

provide a way that allows a customer to upload a picture to request a service call or quote.
Updates

I'm looking for the design to be completed in WordPress

Industry/Entity Type

HVAC Mechanical & Building Automation / Controls contractor

Coding

Coded - Design and coding required

Number of Pages Required

5+ page

Colors
0054AA
0677BA
7BADD7
CADEEF
E8F1F8

Requirements
Must have
• Design a new modern, clean, website for HVAC mechanical business that uses company logo/colors for branding and recognition. Files attached are just for band and color information. Here is a website design that appeals to me https://www.corvellsupply.example/ A clear description of who we are and what we do An easily-navigated site map An easily-navigated site map for mobile devices Easy-to-find contact information Obvious call to action for service, installs or to schedule estimates about us page Provide a way for potential customers to contact us via text or email provide a way that allows a customer to upload a picture to request a service call or quote.
Nice to have

```html
<!DOCTYPE html>
<html lang="en">
<head>
<meta charset="UTF-8">
<title>Pelican HVAC — Heating &amp; Air Conditioning</title>
<link rel="stylesheet" href="https://fonts.googleapis.com/css2?family=Cinzel:wght@500;600&family=Noto+Serif:wght@600;700&family=Open+Sans:wght@400;600;700&family=Roboto:wght@500;700&display=swap">
<style>
:root{
  --navy:#0b2454;
  --navy-deep:#0a1d44;
  --blue:#0054AA;
  --blue-2:#0677BA;
  --blue-3:#7BADD7;
  --blue-4:#CADEEF;
  --blue-5:#E8F1F8;
  --panel:#0d3a78;
  --panel-2:#1560b8;
  --ink:#1b2433;
  --text:#4a5261;
  --white:#ffffff;
  --star:#f5b700;
}
*{box-sizing:border-box;margin:0;padding:0}
html,body{width:1200px;height:5231px;overflow:hidden}
body{font-family:"Open Sans",Arial,sans-serif;color:var(--text);background:var(--white);position:relative}
section,header,footer{position:relative;width:1200px;overflow:hidden}
.abs{position:absolute}
.pill{position:absolute;display:flex;align-items:center;justify-content:center;border-radius:30px;font-family:"Roboto",Arial,sans-serif;font-weight:500;font-size:16px;color:var(--white);background:var(--blue)}
.kicker{position:absolute;left:0;width:1200px;text-align:center;font-family:"Noto Serif",Georgia,serif;font-size:20px;font-weight:600;color:var(--ink);letter-spacing:.5px}
.sec-title{position:absolute;font-family:"Noto Serif",Georgia,serif;font-weight:700;font-size:38px;color:var(--ink);letter-spacing:.5px}
.sec-title .accent{color:var(--blue)}
.center{left:0;width:1200px;text-align:center}

/* header */
.site-header{height:108px;background:var(--white);z-index:5}
.brand{position:absolute;left:100px;top:30px;display:flex;align-items:center;gap:12px;z-index:6}
.brand-dot{width:46px;height:46px;border-radius:50%;background:var(--blue)}
.brand-name{font-family:"Noto Serif",Georgia,serif;font-weight:700;font-size:30px;color:var(--navy)}
.topbar{position:absolute;left:700px;top:0;width:420px;height:45px;background:var(--navy);clip-path:polygon(22px 0,100% 0,calc(100% - 22px) 100%,0 100%);display:flex;align-items:center;padding-left:40px;gap:22px}
.social-dot{width:12px;height:12px;border-radius:50%;background:var(--white)}
.topbar .phone{margin-left:26px;display:flex;align-items:center;gap:8px;color:var(--white);font-family:"Roboto",Arial,sans-serif;font-size:17px;font-weight:500}
.main-nav{position:absolute;top:72px;left:449px;display:flex;gap:0;font-family:"Roboto",Arial,sans-serif;font-weight:700;font-size:14.5px;color:var(--ink)}
.main-nav a{position:absolute;white-space:nowrap;color:var(--ink);text-decoration:none}
.main-nav a.active::after{content:"";position:absolute;left:0;right:0;bottom:-12px;height:3px;background:var(--blue)}

/* hero */
.hero{height:704px}
.hero-photo{position:absolute;inset:0 0 110px 0;background:linear-gradient(180deg,#3a4656 0%,#52617a 35%,#3b4a63 65%,#2a3648 100%)}
.hero-curve{position:absolute;left:0;bottom:0;width:1200px;height:260px}
.hero-title{position:absolute;left:0;top:175px;width:1200px;text-align:center;font-family:"Cinzel",Georgia,serif;font-weight:600;font-size:64px;line-height:68px;color:var(--white);letter-spacing:2px}
.hero-line{position:absolute;left:470px;top:359px;width:50px;height:3px;background:var(--blue)}
.hero-btn{left:532px;top:338px;width:193px;height:46px;justify-content:flex-start;padding-left:30px;font-size:17px}
.btn-arrow{position:absolute;right:6px;top:6px;width:34px;height:34px;border-radius:50%;background:rgba(255,255,255,.2);display:flex;align-items:center;justify-content:center}
.hero-van{position:absolute;left:274px;top:460px;width:600px;height:234px;border-radius:60px 120px 40px 40px;background:linear-gradient(180deg,#eef1f5 0%,#c8d2de 60%,#2f5ea8 100%)}

/* about */
.about{height:646px}
.about-photo{position:absolute;left:81px;top:81px;width:481px;height:481px;border-radius:50%;border:6px solid var(--blue);padding:8px;background:var(--white)}
.about-photo .fill{width:100%;height:100%;border-radius:50%;background:linear-gradient(135deg,#c9d1db 0%,#8b9aae 50%,#2b4d8a 100%)}
.about-badge{position:absolute;left:116px;top:85px;width:122px;height:122px;border-radius:50%;background:var(--white);border:5px solid var(--navy)}
.about-title{left:641px;top:140px}
.title-wave{position:absolute}
.about-copy{position:absolute;left:641px;top:216px;width:460px;font-size:17.5px;line-height:29px;color:#3d4452}
.about-copy p+p{margin-top:14px}
.about-btn{left:641px;top:495px;width:186px;height:52px}

/* service cards */
.services-cards{height:832px;background:#eef2f7}
.card{position:absolute;top:174px;width:484px;height:540px}
.card-photo{height:286px;background:linear-gradient(135deg,#cfd7e0,#6f87a6 70%,#1d4f9c)}
.card-body{height:254px;text-align:center;color:var(--white);padding-top:38px}
.card-body h3{font-family:"Open Sans",Arial,sans-serif;font-weight:700;font-size:18px;letter-spacing:.3px}
.card-body p{margin:16px auto 0;width:380px;font-size:14px;line-height:23px}
.card-btn{position:relative;margin:26px auto 0;width:150px;height:44px;border-radius:24px;background:var(--navy);display:flex;align-items:center;justify-content:center;font-family:"Roboto",Arial,sans-serif;font-weight:500;font-size:14px}

/* service list */
.services-list{height:776px}
.hub-ring{position:absolute;left:100px;top:212px;width:470px;height:470px;border-radius:50%;border:1.5px solid #d6dde7}
.hub-photo{position:absolute;left:128px;top:248px;width:410px;height:426px;border-radius:50%;background:linear-gradient(160deg,#1e4f99,#163c78 60%,#0d2b5c)}
.hub-name{position:absolute;left:230px;top:420px;width:210px;height:76px;border-radius:40px;border:3px solid var(--white);display:flex;align-items:center;justify-content:center;font-family:"Noto Serif",Georgia,serif;font-weight:700;font-size:26px;color:var(--white)}
.hub-van{position:absolute;left:132px;top:532px;width:416px;height:172px;border-radius:40px 90px 30px 30px;background:linear-gradient(180deg,#f0f3f7,#c5cfdb 60%,#2f5ea8)}
.hub-dot{position:absolute;width:12px;height:12px;border-radius:50%;background:var(--blue)}
.svc-icon{position:absolute;width:82px;height:82px;border-radius:50%;background:var(--white);border:1.5px solid #d9e0ea;display:flex;align-items:center;justify-content:center}
.svc-item{position:absolute;width:420px}
.svc-item h4{font-family:"Open Sans",Arial,sans-serif;font-weight:600;font-size:19px;color:var(--ink)}
.svc-item p{margin-top:6px;font-size:14px;line-height:22px;color:#6a7180}

/* why */
.why{height:528px;background:#e9eff7}
.why-photo{position:absolute;left:0;top:0;width:1200px;height:528px;background:linear-gradient(120deg,#8a96a6,#a5552e 55%,#2852a0);clip-path:polygon(795px 0,1200px 0,1200px 528px,505px 528px)}
.why-title{left:101px;top:78px}
.why-lead{position:absolute;left:101px;top:170px;width:430px;font-family:"Open Sans",Arial,sans-serif;font-size:23px;line-height:31px;color:var(--ink)}
.why-copy{position:absolute;left:101px;top:254px;width:460px;font-size:17.5px;line-height:29px;color:#3d4452}
.why-btn{left:101px;top:395px;width:186px;height:52px}

/* testimonials */
.testimonials{height:491px;background:#123e80}
.testi-wash{position:absolute;inset:0;background:linear-gradient(110deg,#1b58b0 0%,#1b58b0 30%,#143f86 48%,#0f3470 100%);clip-path:polygon(0 0,430px 0,260px 491px,0 491px)}
.testi-back{position:absolute;inset:0;background:linear-gradient(180deg,#0f3470,#0d2f66)}
.testi-kicker{position:absolute;left:101px;top:95px;font-size:21px;color:var(--white)}
.testi-title{position:absolute;left:101px;top:132px;font-family:"Noto Serif",Georgia,serif;font-weight:700;font-size:36px;line-height:46px;color:var(--white)}
.testi-btn{left:99px;top:235px;width:258px;height:46px;background:var(--white);color:var(--ink);font-size:15px}
.testi-van{position:absolute;left:51px;top:325px;width:416px;height:163px;border-radius:40px 90px 30px 30px;background:linear-gradient(180deg,#f0f3f7,#c5cfdb 60%,#2f5ea8)}
.quote-card{position:absolute;top:112px;width:302px;height:233px;background:var(--white);border-radius:4px;padding:26px 24px;box-shadow:0 6px 0 #0a2a5e}
.quote-card p{font-style:italic;font-size:12px;line-height:21px;color:#5b6270}
.quote-who{display:flex;align-items:center;gap:10px;margin-top:18px}
.avatar{width:30px;height:30px;border-radius:50%;background:#c9d1dc}
.who-name{font-family:"Roboto",Arial,sans-serif;font-weight:700;font-size:11px;color:var(--ink)}
.stars{display:flex;gap:2px;margin-top:3px}

/* quote + map */
.quote-map{height:500px}
.map{position:absolute;inset:0;background:linear-gradient(135deg,#eef1ee,#e2e8e2 50%,#dde6ee)}
.quote-form{position:absolute;left:122px;top:53px;width:357px;height:406px;background:var(--navy);border-radius:10px;padding:30px 28px}
.quote-form h2{font-family:"Open Sans",Arial,sans-serif;font-weight:600;font-size:18px;line-height:22px;color:var(--white)}
.form-wave{margin:6px 0 16px}
.field{height:37px;margin-bottom:10px;background:var(--white);border-radius:2px;padding:0 12px;display:flex;align-items:center;justify-content:space-between;font-size:13px;color:#7a8190}
.send{height:42px;margin-top:6px;background:var(--blue);display:flex;align-items:center;justify-content:center;color:var(--white);font-family:"Roboto",Arial,sans-serif;font-weight:500;font-size:16px}

/* partners */
.partners{height:111px;background:var(--white);display:flex;align-items:center;justify-content:center;gap:56px}
.partner-badge{width:138px;height:30px;border-radius:15px;background:#c8ccd2}

/* footer */
.site-footer{height:535px;background:var(--navy-deep);color:var(--white)}
.foot-brand{position:absolute;left:101px;top:85px;display:flex;align-items:center;gap:12px}
.foot-brand .brand-name{color:var(--white)}
.foot-brand .brand-dot{background:var(--white)}
.foot-tag{position:absolute;left:780px;top:84px;font-family:"Open Sans",Arial,sans-serif;font-size:27px;line-height:40px;letter-spacing:.5px}
.foot-head{position:absolute;top:200px;font-family:"Open Sans",Arial,sans-serif;font-weight:700;font-size:16px}
.foot-rule{position:absolute;left:392px;top:216px;width:1px;height:210px;background:rgba(255,255,255,.18)}
.contact-row{position:absolute;left:99px;display:flex;gap:20px;align-items:flex-start}
.contact-ico{width:48px;height:48px;border-radius:4px;background:var(--blue);display:flex;align-items:center;justify-content:center}
.contact-row b{display:block;font-size:15px;font-weight:600}
.contact-row span{font-size:14px;color:#d0d8e6}
.foot-links{position:absolute;left:473px;top:248px;list-style:none}
.foot-links li{display:flex;align-items:center;gap:10px;height:25.5px;font-size:14px;color:#c3cbd8}
.foot-links li::before{content:"";width:10px;height:10px;border-radius:50%;background:#8e9ab0}
.news-input{position:absolute;left:769px;top:235px;width:329px;height:45px;border-radius:24px;background:#132c5e;padding-left:30px;display:flex;align-items:center;font-size:14px;color:#8f9bb3}
.news-btn{left:769px;top:296px;width:142px;height:44px;justify-content:flex-start;padding-left:26px;font-size:15px}
.news-btn .btn-arrow{width:32px;height:32px;top:6px}
.foot-bottom{position:absolute;left:101px;right:101px;top:460px;height:1px;background:rgba(255,255,255,.15)}
.copyright{position:absolute;left:101px;top:486px;font-size:13px;color:#b5bfcf}
.legal{position:absolute;left:387px;top:486px;font-size:13px;color:#d5dce8}
.foot-social{position:absolute;left:993px;top:481px;display:flex;gap:10px}
.foot-social span{width:26px;height:26px;border-radius:50%;background:var(--white)}
</style>
</head>
<body>

<header class="site-header">
  <div class="brand"><span class="brand-dot"></span><span class="brand-name">Pelican HVAC</span></div>
  <div class="topbar">
    <span class="social-dot"></span><span class="social-dot"></span><span class="social-dot"></span><span class="social-dot"></span>
    <span class="phone">
      <svg width="16" height="16" viewBox="0 0 24 24" fill="none" stroke="#fff" stroke-width="2"><path d="M22 16.9v3a2 2 0 0 1-2.2 2 19.8 19.8 0 0 1-8.6-3.1 19.5 19.5 0 0 1-6-6A19.8 19.8 0 0 1 2.1 4.2 2 2 0 0 1 4.1 2h3a2 2 0 0 1 2 1.7c.1 1 .4 1.9.7 2.8a2 2 0 0 1-.5 2.1L8 9.9a16 16 0 0 0 6 6l1.3-1.3a2 2 0 0 1 2.1-.4c.9.3 1.8.6 2.8.7a2 2 0 0 1 1.7 2z"/></svg>
      (555) 014 2277
    </span>
  </div>
  <nav class="main-nav">
    <a class="active" style="left:0">HOME</a>
    <a style="left:81px">OUR SERVICES</a>
    <a style="left:229px">ABOUT US</a>
    <a style="left:345px">TESTIMONIALS</a>
    <a style="left:495px">BLOG</a>
    <a style="left:572px">CONTACT</a>
  </nav>
</header>

<section class="hero">
  <div class="hero-photo" role="img" aria-label="City skyline at dusk"></div>
  <svg class="hero-curve" viewBox="0 0 1200 260" preserveAspectRatio="none">
    <path d="M0 110 Q600 300 1200 110 L1200 260 L0 260 Z" fill="#fff"/>
  </svg>
  <h1 class="hero-title">HEATING &amp; AIR<br>CONDITIONING</h1>
  <span class="hero-line"></span>
  <a class="pill hero-btn">LEARN MORE<span class="btn-arrow"><svg width="12" height="14" viewBox="0 0 12 14" fill="none" stroke="#fff" stroke-width="2"><path d="M3 1l6 6-6 6"/></svg></span></a>
  <div class="hero-van" role="img" aria-label="Company service van with branded livery"></div>
</section>

<section class="about">
  <div class="about-photo"><div class="fill" role="img" aria-label="Technician drilling into an indoor air conditioning unit"></div></div>
  <div class="about-badge"></div>
  <h2 class="sec-title about-title"><span class="accent">ABOUT</span> PELICAN</h2>
  <svg class="title-wave" style="left:641px;top:193px" width="96" height="10" viewBox="0 0 96 10"><path d="M2 6 Q14 0 26 5 T50 5 T74 5 T94 4" fill="none" stroke="#0054AA" stroke-width="2.5"/></svg>
  <div class="about-copy">
    <p>Lorem ipsum is simply dummy text of the printing and typesetting industry. Lorem Ipsum has been the industry's standard dummy text ever since the 1500s, when an unknown printer.</p>
    <p>when an unknown printer took a galley of type and scrambled it to make a type specimen book. It has survived not only five centuries, but also the leap into electronic typesetting.</p>
  </div>
  <a class="pill about-btn">LEARN MORE</a>
</section>

<section class="services-cards">
  <div class="kicker" style="top:52px">WHAT WE DO</div>
  <h2 class="sec-title center" style="top:80px"><span class="accent">OUR</span> SERVICES</h2>
  <svg class="title-wave" style="left:552px;top:134px" width="96" height="10" viewBox="0 0 96 10"><path d="M2 6 Q14 0 26 5 T50 5 T74 5 T94 4" fill="none" stroke="#0054AA" stroke-width="2.5"/></svg>
  <article class="card" style="left:99px">
    <div class="card-photo" role="img" aria-label="Two technicians servicing an outdoor condenser unit"></div>
    <div class="card-body" style="background:var(--panel)">
      <h3>AIR CONDITIONING</h3>
      <p>Lorem Ipsum is simply dummy text of the printing and typesetting industry. Lorem Ipsum has been the industry's standard dummy text ever since.</p>
      <div class="card-btn">LEARN MORE</div>
    </div>
  </article>
  <article class="card" style="left:615px">
    <div class="card-photo" role="img" aria-label="Technician installing an outdoor heat pump unit"></div>
    <div class="card-body" style="background:var(--panel-2)">
      <h3>ABOUT HEATING</h3>
      <p>Lorem Ipsum is simply dummy text of the printing and typesetting industry. Lorem Ipsum has been the industry's standard dummy text ever since.</p>
      <div class="card-btn">LEARN MORE</div>
    </div>
  </article>
</section>

<section class="services-list">
  <div class="kicker" style="top:73px">WHAT WE DO</div>
  <h2 class="sec-title center" style="top:100px"><span class="accent">OUR</span> SERVICES</h2>
  <svg class="title-wave" style="left:552px;top:154px" width="96" height="10" viewBox="0 0 96 10"><path d="M2 6 Q14 0 26 5 T50 5 T74 5 T94 4" fill="none" stroke="#0054AA" stroke-width="2.5"/></svg>

  <div class="hub-ring"></div>
  <div class="hub-photo" role="img" aria-label="Blue city backdrop"></div>
  <div class="hub-name">Pelican HVAC</div>
  <div class="hub-van" role="img" aria-label="Company service van"></div>
  <span class="hub-dot" style="left:486px;top:271px"></span>
  <span class="hub-dot" style="left:538px;top:343px"></span>
  <span class="hub-dot" style="left:554px;top:464px"></span>
  <span class="hub-dot" style="left:525px;top:594px"></span>

  <div class="svc-icon" style="left:514px;top:190px">
    <svg width="44" height="44" viewBox="0 0 48 48" fill="none" stroke="#0054AA" stroke-width="2"><circle cx="24" cy="24" r="4"/><path d="M24 20c-2-8 4-14 9-11s2 10-5 12M28 24c8-2 14 4 11 9s-10 2-12-5M24 28c2 8-4 14-9 11s-2-10 5-12M20 24c-8 2-14-4-11-9s10-2 12 5"/></svg>
  </div>
  <div class="svc-item" style="left:619px;top:198px"><h4>AIR CONDITIONING</h4><p>Lorem ipsum is simply dummy text of the printing and<br>typesetting industry.</p></div>

  <div class="svc-icon" style="left:582px;top:304px">
    <svg width="40" height="44" viewBox="0 0 40 44" fill="none" stroke="#0054AA" stroke-width="2"><path d="M20 3c2 8 12 13 12 24a12 12 0 0 1-24 0c0-6 3-9 5-12 1 4 3 6 5 6-2-7 0-13 2-18z"/><path d="M20 40a5 5 0 0 1-5-5c0-3 3-5 5-9 2 4 5 6 5 9a5 5 0 0 1-5 5z"/></svg>
  </div>
  <div class="svc-item" style="left:688px;top:312px"><h4>HEATING</h4><p>Lorem ipsum is simply dummy text of the printing and<br>typesetting industry.</p></div>

  <div class="svc-icon" style="left:582px;top:426px">
    <svg width="44" height="44" viewBox="0 0 48 48" fill="none" stroke="#0054AA" stroke-width="2"><circle cx="24" cy="12" r="7"/><path d="M24 19v6M12 25h24v8H12zM16 33v10M32 33v10M8 43h32M19 12h10"/></svg>
  </div>
  <div class="svc-item" style="left:688px;top:434px"><h4>GAS FITTING</h4><p>Lorem ipsum is simply dummy text of the printing and<br>typesetting industry.</p></div>

  <div class="svc-icon" style="left:548px;top:556px">
    <svg width="42" height="42" viewBox="0 0 48 48" fill="none" stroke="#0054AA" stroke-width="2"><path d="M8 40l18-18M30 8a8 8 0 0 0-6 11l-2 2 5 5 2-2a8 8 0 0 0 11-6l-5 1-4-4 1-5zM40 40L26 26M8 8l6 2 2 6 6 6"/></svg>
  </div>
  <div class="svc-item" style="left:654px;top:564px"><h4>PUMPS</h4><p>Lorem ipsum is simply dummy text of the printing and<br>typesetting industry.</p></div>
</section>

<section class="why">
  <div class="why-photo" role="img" aria-label="Technician fitting valves on a boiler manifold"></div>
  <h2 class="sec-title why-title"><span class="accent">WHY</span> CHOOSE US</h2>
  <svg class="title-wave" style="left:101px;top:133px" width="96" height="10" viewBox="0 0 96 10"><path d="M2 6 Q14 0 26 5 T50 5 T74 5 T94 4" fill="none" stroke="#0054AA" stroke-width="2.5"/></svg>
  <p class="why-lead">Lorem ipsum is simply dummy text of the printing</p>
  <p class="why-copy">when an unknown printer took a galley of type and scrambled it to make a type specimen book. It has survived not only five centuries, but also the leap into electronic typesetting.</p>
  <a class="pill why-btn">LEARN MORE</a>
</section>

<section class="testimonials">
  <div class="testi-back" role="img" aria-label="Dimmed blue technician backdrop"></div>
  <div class="testi-wash"></div>
  <p class="testi-kicker">Testimonials</p>
  <h2 class="testi-title">WHAT OUR<br>CUSTOMER SAYS</h2>
  <a class="pill testi-btn">SCHEDULE AN APPOINTMENT</a>
  <div class="testi-van" role="img" aria-label="Company service van"></div>

  <div class="quote-card" style="left:463px">
    <p>"Lorem ipsum dolor sit amet, consectetur adipiscing elit, sed do eiusmod tempor incididunt ut labore et dolore magna aliqua. Ut enim ad iqua. Ut enim ad minim veniam, quis nostrud exercitation"</p>
    <div class="quote-who"><span class="avatar"></span><div><div class="who-name">DANA WHITLEY</div>
      <div class="stars"><svg width="70" height="12" viewBox="0 0 70 12" fill="#f5b700"><path id="st" d="M6 0l1.8 3.9 4.2.4-3.2 2.8 1 4.1L6 9.1 2.2 11.2l1-4.1L0 4.3l4.2-.4z"/><use href="#st" x="14"/><use href="#st" x="28"/><use href="#st" x="42"/><use href="#st" x="56"/></svg></div></div></div>
  </div>
  <div class="quote-card" style="left:796px">
    <p>"Lorem ipsum dolor sit amet, consectetur adipiscing elit, sed do eiusmod tempor incididunt ut labore et dolore magna aliqua. Ut enim ad iqua. Ut enim ad minim veniam, quis nostrud exercitation"</p>
    <div class="quote-who"><span class="avatar"></span><div><div class="who-name">DANA WHITLEY</div>
      <div class="stars"><svg width="70" height="12" viewBox="0 0 70 12" fill="#f5b700"><path id="st2" d="M6 0l1.8 3.9 4.2.4-3.2 2.8 1 4.1L6 9.1 2.2 11.2l1-4.1L0 4.3l4.2-.4z"/><use href="#st2" x="14"/><use href="#st2" x="28"/><use href="#st2" x="42"/><use href="#st2" x="56"/></svg></div></div></div>
  </div>
</section>

<section class="quote-map">
  <div class="map" role="img" aria-label="Street map of the service area"></div>
  <form class="quote-form">
    <h2>Request A Quote / Book Our<br>Service</h2>
    <svg class="form-wave" width="30" height="8" viewBox="0 0 30 8"><path d="M1 5 Q5 1 9 4 T17 4 T25 4 T29 3" fill="none" stroke="#7BADD7" stroke-width="2"/></svg>
    <div class="field">Name</div>
    <div class="field">Phone</div>
    <div class="field">Email Address</div>
    <div class="field">Choose Services<svg width="12" height="8" viewBox="0 0 12 8" fill="none" stroke="#7a8190" stroke-width="1.6"><path d="M1 1l5 5 5-5"/></svg></div>
    <div class="field">Upload Image<svg width="20" height="14" viewBox="0 0 24 16" fill="none" stroke="#7a8190" stroke-width="1.6"><path d="M6 15a5 5 0 0 1-.5-10A7 7 0 0 1 19 6a4.5 4.5 0 0 1-1 9z"/><path d="M12 13V7M9.5 9.5L12 7l2.5 2.5"/></svg></div>
    <div class="send">SEND MESSAGE</div>
  </form>
</section>

<section class="partners">
  <span class="partner-badge"></span><span class="partner-badge"></span><span class="partner-badge"></span>
  <span class="partner-badge"></span><span class="partner-badge"></span><span class="partner-badge"></span>
</section>

<footer class="site-footer">
  <div class="foot-brand"><span class="brand-dot"></span><span class="brand-name">Pelican HVAC</span></div>
  <p class="foot-tag">QUALITY AIR<br>CONDITIONING SERVICE</p>

  <h3 class="foot-head" style="left:99px">CONTACT</h3>
  <div class="contact-row" style="top:262px">
    <span class="contact-ico"><svg width="24" height="18" viewBox="0 0 24 18" fill="none" stroke="#fff" stroke-width="1.8"><rect x="1" y="1" width="22" height="16" rx="2"/><path d="M1 2l11 8 11-8"/></svg></span>
    <div style="padding-top:4px"><b>Email:</b><span>hello@pelicanhvac.example</span></div>
  </div>
  <div class="contact-row" style="top:358px">
    <span class="contact-ico"><svg width="22" height="22" viewBox="0 0 24 24" fill="none" stroke="#fff" stroke-width="1.8"><path d="M22 16.9v3a2 2 0 0 1-2.2 2 19.8 19.8 0 0 1-8.6-3.1 19.5 19.5 0 0 1-6-6A19.8 19.8 0 0 1 2.1 4.2 2 2 0 0 1 4.1 2h3a2 2 0 0 1 2 1.7c.1 1 .4 1.9.7 2.8a2 2 0 0 1-.5 2.1L8 9.9a16 16 0 0 0 6 6l1.3-1.3a2 2 0 0 1 2.1-.4c.9.3 1.8.6 2.8.7a2 2 0 0 1 1.7 2z"/></svg></span>
    <div style="padding-top:4px"><b>Call Us:</b><span>555 014 2277</span></div>
  </div>

  <span class="foot-rule"></span>
  <h3 class="foot-head" style="left:473px">LINKS</h3>
  <ul class="foot-links">
    <li>Home</li><li>About Us</li><li>Services</li><li>Blog</li><li>Sitemap</li><li>Location</li><li>Contact Us</li>
  </ul>

  <h3 class="foot-head" style="left:784px">OUR NEWS LETTER</h3>
  <div class="news-input">Enter Your email....</div>
  <a class="pill news-btn">SUBMIT<span class="btn-arrow"><svg width="10" height="12" viewBox="0 0 12 14" fill="none" stroke="#fff" stroke-width="2"><path d="M3 1l6 6-6 6"/></svg></span></a>

  <span class="foot-bottom"></span>
  <p class="copyright">Copyright @ Pelican HVAC 2024</p>
  <p class="legal">Cookie policy &nbsp;&nbsp;|&nbsp;&nbsp; Terms of Condition</p>
  <div class="foot-social"><span></span><span></span><span></span></div>
</footer>

</body>
</html>
```